New Bicycle shop business card

Hi!
I'm looking for a business card for my new proffesional bike mechanics shop. This shop is only for fixing broken bikes and not selling bikes.
Peferbly a modern and sleek and modern design.
Colors: black, grey, red, white
Information:
Name: Rijwielwerkplaats Vanhoutte
Shop owner: Bart Vanhoutte & Marieke Segers
Website: www.rijwielwerkplaats-vanhoutte.be
Email: info@rijwielwerkplaats-vanhoutte.be
Phone number: +32471902368
Street adres: Kerkweg 46
9940 Bellebeke
Slogan/shop information: Herstellingen van alle merken.
Logo: see files.
Target Market(s)
People who seek a mechanic to fix or upgrade their bikes.
Contact Information for Business Card
Information:
Website: info@rijwielwerkplaats-vanhoutte.be
9940 Bellebeke
Logo: see files.

```html
<!DOCTYPE html>
<html lang="nl">
<head>
<meta charset="utf-8">
<title>Rijwielwerkplaats Vanhoutte – visitekaartjes</title>
<link href="https://fonts.googleapis.com/css2?family=Open+Sans:ital,wght@0,400;0,600;0,700;0,800;1,600&display=swap" rel="stylesheet">
<style>
  :root {
    --black: #0a0a0c;
    --red: #e8203f;
    --white: #ffffff;
    --grey: #b9b9bd;
    --backdrop: #3a3b3f;
  }
  html, body {
    margin: 0;
    padding: 0;
    width: 1200px;
    height: 900px;
    overflow: hidden;
    background: var(--backdrop);
    font-family: "Open Sans", Arial, sans-serif;
  }
  .sheet {
    position: relative;
    width: 1200px;
    height: 900px;
  }
  .card {
    position: absolute;
    left: 270px;
    width: 660px;
    height: 378px;
    overflow: hidden;
    box-shadow: 0 10px 30px rgba(0,0,0,.45);
  }
  .card--front { top: 48px; background: var(--black); }
  .card--back  { top: 474px; background: var(--black); }

  p { margin: 0; }

  /* front */
  .front-edge {
    position: absolute;
    left: 0; bottom: 0;
    width: 100%; height: 8px;
    background: var(--red);
  }
  .brand {
    position: absolute;
    display: flex;
    align-items: center;
    gap: 14px;
  }
  .brand__mark {
    width: 38px; height: 38px;
    background: var(--red);
    flex: none;
  }
  .brand__name {
    font-weight: 800;
    text-transform: uppercase;
    letter-spacing: .04em;
    line-height: 1.05;
    white-space: nowrap;
  }
  .card--front .brand {
    left: 0; right: 0; top: 128px;
    justify-content: center;
  }
  .card--front .brand__name {
    color: var(--white);
    font-size: 30px;
  }
  .tagline {
    position: absolute;
    left: 0; right: 0; top: 252px;
    text-align: center;
    color: var(--white);
    font-size: 15px;
    font-weight: 600;
  }

  /* back */
  .back-shape { position: absolute; inset: 0; }
  .contact {
    position: absolute;
    left: 34px; top: 34px;
    width: 320px;
    color: var(--white);
  }
  .contact__label {
    color: var(--red);
    font-style: italic;
    font-weight: 600;
    font-size: 13px;
  }
  .contact__owners {
    font-weight: 700;
    font-size: 15px;
    margin: 2px 0 10px;
  }
  .dash {
    width: 10px; height: 3px;
    background: var(--red);
    margin: 0 0 12px;
  }
  .contact__company {
    color: var(--red);
    font-weight: 700;
    font-size: 15px;
  }
  .contact__role {
    color: var(--grey);
    font-size: 11px;
    font-weight: 600;
    margin: 2px 0 12px;
  }
  .contact__list {
    list-style: none;
    margin: 0 0 12px;
    padding: 0;
    font-size: 12px;
    color: var(--grey);
  }
  .contact__list li {
    display: flex;
    align-items: center;
    gap: 8px;
    margin-bottom: 5px;
  }
  .contact__list svg { width: 11px; height: 11px; flex: none; }
  .contact__address {
    font-size: 12px;
    color: var(--grey);
  }
  .card--back .brand {
    left: 400px; top: 140px;
    width: 236px;
    flex-direction: column;
    gap: 12px;
    text-align: center;
  }
  .card--back .brand__name {
    color: var(--black);
    font-size: 17px;
  }
  .card--back .brand__mark { width: 32px; height: 32px; }
</style>
</head>
<body>
<main class="sheet">

  <section class="card card--front" aria-label="Voorzijde visitekaartje">
    <div class="brand">
      <span class="brand__mark"></span>
      <span class="brand__name">Rijwielwerkplaats<br>Vanhoutte</span>
    </div>
    <p class="tagline">Herstellingen van alle merken.</p>
    <div class="front-edge"></div>
  </section>

  <section class="card card--back" aria-label="Achterzijde visitekaartje">
    <svg class="back-shape" viewBox="0 0 660 378" width="660" height="378" aria-hidden="true">
      <path d="M428,0 C348,90 338,260 378,378 L660,378 L660,0 Z" fill="var(--red)"/>
      <path d="M440,0 C358,92 348,262 390,378 L660,378 L660,0 Z" fill="var(--white)"/>
    </svg>

    <div class="contact">
      <p class="contact__label">Shop owner:</p>
      <p class="contact__owners">Bart Vanhoutte &amp; Marieke Segers</p>
      <div class="dash"></div>
      <p class="contact__company">Rijwielwerkplaats Vanhoutte</p>
      <p class="contact__role">General Manager</p>
      <ul class="contact__list">
        <li>
          <svg viewBox="0 0 12 12"><path d="M2.5 1 L4.5 1 L5.3 3.4 L4 4.4 C4.7 5.9 6 7.2 7.6 8 L8.6 6.7 L11 7.5 L11 9.5 C11 10.3 10.3 11 9.5 11 C5 11 1 7 1 2.5 C1 1.7 1.7 1 2.5 1 Z" fill="var(--red)"/></svg>
          +32471902368
        </li>
        <li>
          <svg viewBox="0 0 12 12"><rect x="1" y="2.5" width="10" height="7" fill="var(--red)"/><path d="M1 2.5 L6 6.5 L11 2.5" stroke="var(--black)" stroke-width="1" fill="none"/></svg>
          info@rijwielwerkplaats-vanhoutte.be
        </li>
        <li>
          <svg viewBox="0 0 12 12"><circle cx="6" cy="6" r="5" fill="var(--red)"/><path d="M1 6 H11 M6 1 C3.5 4 3.5 8 6 11 M6 1 C8.5 4 8.5 8 6 11" stroke="var(--black)" stroke-width=".8" fill="none"/></svg>
          www.rijwielwerkplaats-vanhoutte.be
        </li>
      </ul>
      <div class="dash"></div>
      <p class="contact__address">Kerkweg 46 9940 Bellebeke</p>
    </div>

    <div class="brand">
      <span class="brand__mark"></span>
      <span class="brand__name">Rijwielwerkplaats<br>Vanhoutte</span>
    </div>
  </section>

</main>
</body>
</html>
```